Business Card Design needed for start up company Halvora

In need of a new business card designed for a start up company based in Sydney, Halvora is a new start up innovative Company, our mission it to make property accessible for everyday Australian and to become the leading Real Estate platform in Australia. We want it to be fresh and clean.

Industry/Entity Type

Financial

Contact Information for Business Card

Section for Name
Section for Title

HALVORA - The Strength of Pooling
Mobile:
Direct:

Font styles to use
Sans Serif

Colors
33a6d7
0692cd
0255a3
ffffff

Requirements
Must have
• Logo, all business card details

```html
<!DOCTYPE html>
<html lang="en">
<head>
<meta charset="utf-8">
<title>Halvora Business Card</title>
<link rel="stylesheet" href="https://fonts.googleapis.com/css2?family=Open+Sans:wght@400;600;700&display=swap">
<style>
  :root {
    --sky: #33a6d7;
    --ocean: #0692cd;
    --navy: #0255a3;
    --deep: #163a72;
    --white: #ffffff;
    --stage: #e6e9ee;
    --ink-soft: #dbe9f6;
  }
  * { margin: 0; padding: 0; box-sizing: border-box; }
  html, body {
    width: 1200px; height: 900px; overflow: hidden;
    background: var(--stage);
    font-family: "Open Sans", Arial, sans-serif;
  }
  .stage {
    width: 1200px; height: 900px;
    display: flex; flex-direction: column;
    align-items: center; justify-content: center; gap: 40px;
  }
  .card {
    position: relative;
    width: 700px; height: 400px;
    overflow: hidden;
    box-shadow: 0 14px 30px rgba(20, 40, 80, 0.18);
  }

  /* Front */
  .card-front {
    background: linear-gradient(120deg, #2a5fb0 0%, var(--navy) 35%, var(--deep) 100%);
    color: var(--white);
  }
  .brand-name {
    font-weight: 700; letter-spacing: 3px; line-height: 1;
  }
  .front-brand {
    position: absolute; left: 0; right: 0; top: 158px;
    text-align: center; font-size: 56px;
  }
  .tagline {
    position: absolute; left: 0; right: 0; top: 262px;
    text-align: center; font-size: 15px; color: var(--ink-soft);
  }

  /* Back */
  .card-back { background: var(--white); }
  .wave { position: absolute; inset: 0; width: 700px; height: 400px; }
  .back-brand {
    position: absolute; left: 60px; top: 158px;
    color: var(--navy); font-size: 50px;
  }

  .contact {
    position: absolute; right: 34px; top: 62px;
    color: var(--white); text-align: right;
    font-size: 14px; line-height: 1.45;
  }
  .contact-name { font-weight: 700; font-size: 18px; letter-spacing: 0.5px; line-height: 1.2; }
  .contact-title { font-size: 15px; margin-bottom: 14px; }
  .contact-line { display: flex; justify-content: flex-end; align-items: center; gap: 10px; }
  .contact-line .icon { width: 14px; height: 14px; flex: none; }
  .contact-line .spacer { width: 14px; flex: none; }
</style>
</head>
<body>
<main class="stage">

  <section class="card card-front" aria-label="Card front">
    <p class="brand-name front-brand">HALVORA</p>
    <p class="tagline">The Strength of Pooling</p>
  </section>

  <section class="card card-back" aria-label="Card back">
    <svg class="wave" viewBox="0 0 700 400" aria-hidden="true">
      <path d="M540,0 C420,50 470,250 350,330 C270,383 120,372 0,372 L0,400 L700,400 L700,0 Z" fill="var(--sky)"/>
      <path d="M568,0 C450,55 500,262 385,340 C300,395 140,388 0,388 L0,400 L700,400 L700,0 Z" fill="var(--ocean)"/>
      <path d="M556,0 C436,52 486,256 368,335" fill="none" stroke="var(--white)" stroke-width="3"/>
    </svg>

    <p class="brand-name back-brand">HALVORA</p>

    <div class="contact">
      <p class="contact-name">MARCUS ELDEN</p>
      <p class="contact-title">CEO/FOUNDER</p>
      <p class="contact-line"><span>412 Harbour Row</span>
        <svg class="icon" viewBox="0 0 16 16"><path d="M8 1a5 5 0 0 0-5 5c0 4 5 9 5 9s5-5 5-9a5 5 0 0 0-5-5zm0 7a2 2 0 1 1 0-4 2 2 0 0 1 0 4z" fill="var(--white)"/></svg></p>
      <p class="contact-line"><span>Sydney, NSW 2000</span><span class="spacer"></span></p>
      <p class="contact-line"><span>02 8145 3926</span>
        <svg class="icon" viewBox="0 0 16 16"><path d="M4 1l2.5 3-1.5 2c1 2 3 4 5 5l2-1.5 3 2.5-1.5 2.5C7 15 1 9 1.5 3.5z" fill="var(--white)"/></svg></p>
      <p class="contact-line"><span>0412 657 839</span>
        <svg class="icon" viewBox="0 0 16 16"><rect x="4" y="1" width="8" height="14" rx="1.5" fill="none" stroke="var(--white)" stroke-width="1.6"/><circle cx="8" cy="12.5" r="0.9" fill="var(--white)"/></svg></p>
      <p class="contact-line"><span>marcus@halvora.co</span>
        <svg class="icon" viewBox="0 0 16 16"><rect x="1" y="3" width="14" height="10" rx="1" fill="var(--white)"/><path d="M1.5 3.8L8 9l6.5-5.2" fill="none" stroke="var(--ocean)" stroke-width="1.3"/></svg></p>
      <p class="contact-line"><span>www.halvora.co</span>
        <svg class="icon" viewBox="0 0 16 16"><circle cx="8" cy="8" r="6.5" fill="none" stroke="var(--white)" stroke-width="1.4"/><path d="M1.5 8h13M8 1.5c-3 3.5-3 9.5 0 13M8 1.5c3 3.5 3 9.5 0 13" fill="none" stroke="var(--white)" stroke-width="1.1"/></svg></p>
    </div>
  </section>

</main>
</body>
</html>
```